Quill Harbor (IT/Network Services)

Quill Harbor, LLC provides technology services to small and medium businesses. Essentially, anytime you've every thought your business might need an "IT guy" to handle something you could instead call us to handle it. Basically, you can outsource your IT needs to us.

This is a brand new company and so we'll need a brand new website. I'd like to use WordPress to handle the site since that will make things easier for me to maintain in the long run.

The site should include a, more-or-less, static front page with the dynamic data occurring on pages linked from a navigational area.

I have a logo already designed that I would like to see used in the design. The one with "white" in the title is the official logo, just added some other versions for your perusal.

Color queues from the logo but feel free to add other colors where applicable.

The site should feel somewhat corporate but with a "younger" slant (something a 25-35 year old would enjoy).

Pages (either to be added initially or by me after design completion):
"About" section - includes company history, business philosophy, etc.
"Services" section - service options, service approach, service specifics
"Testimonials" section - (eventually)
"News" section - (eventually) industry news, company news, events, blog
Contact Links

Websites to view:
The two largest local competitors:
http://www.brightmarsh-tech.example/
http://www.kelvarworks.example/
Other local competitors:
http://www.tpbllc.example/
http://www.morrowfield.example/

Other info you might find useful:
Domain: qhllc.example
Address:
417 Elm Row S
Suite 512B
Nashville, TN 37288
Phone: 615-555-0187
Emails available for use/display:
info@qhllc.example
sales@qhllc.example

Target Market(s)

Our target clients are mainly small businesses (25 or less computer users) which means we're looking at a lot of start-ups or younger companies. We'll be interacting with many entrepreneurs and young business owners.

Requirements
Must have
• Need full WP theme (not a mockup)

```html
<!DOCTYPE html>
<html lang="en">
<head>
<meta charset="utf-8">
<title>Quill Harbor — IT &amp; Network Services</title>
<link rel="stylesheet" href="https://fonts.googleapis.com/css2?family=Arimo:wght@400;700&family=Open+Sans:wght@400;600&family=Comic+Neue:wght@700&display=swap">
<style>
:root{
  --ink:#3a3a3a;
  --muted:#666;
  --topbar:#2b2b2b;
  --footer:#282828;
  --orange:#c6580f;
  --orange-light:#d9762a;
  --blue:#1a72b8;
  --green-body:#edf2e8;
  --green-text:#4d8b2b;
  --blue-body:#e6ebef;
  --blue-text:#1f5c9a;
  --amber-body:#f3ece4;
  --amber-text:#c47710;
  --panel-grey:#d3d3d3;
  --tick:#d9501a;
}
*{box-sizing:border-box;margin:0;padding:0}
html,body{width:1200px;height:938px;overflow:hidden;background:#fff}
body{position:relative;font-family:Arimo,Arial,sans-serif;color:var(--ink)}
a{color:inherit;text-decoration:none}
.topbar{position:absolute;left:0;top:0;width:1200px;height:12px;background:var(--topbar)}
.main-nav a{position:absolute;top:12px;height:58px;width:95px;background:linear-gradient(#c65a12,#b84f0a);color:#fff;font-size:16px;text-align:center;line-height:54px;border-bottom:2px solid #fff;box-shadow:0 2px 0 #c96a2a}
.brand{position:absolute;left:135px;top:80px;display:flex;align-items:center;gap:14px}
.brand-mark{width:34px;height:34px;border-radius:50%;background:var(--orange-light)}
.brand-name{font-family:"Open Sans",Arial,sans-serif;font-size:30px;font-weight:600;color:#555;letter-spacing:.5px}
.social{position:absolute;top:135px;left:1092px;display:flex;gap:10px}
.social a{width:26px;height:26px;border-radius:4px}
.social .s1{background:#3b5b9a}.social .s2{background:#3fb0e3}.social .s3{background:#1f78b4}
.hero{position:absolute;left:72px;top:180px;width:1050px;height:262px;background:linear-gradient(#f4f4f4 0,#fff 12%,#fff 80%,#efefef 100%)}
.hero::after{content:"";position:absolute;left:0;right:0;bottom:-3px;height:4px;background:radial-gradient(ellipse at center,#c9c9c9 0,rgba(255,255,255,0) 70%)}
.hero-title{position:absolute;left:90px;top:84px;font-family:"Open Sans",Arial,sans-serif;font-size:29px;color:#444;font-weight:400}
.hero-sub{position:absolute;left:116px;top:130px;font-family:"Comic Neue",cursive;font-size:18px;color:var(--blue)}
.hero-photo{position:absolute;left:583px;top:13px;width:368px;height:241px;background:linear-gradient(90deg,#2a2a2a,#6b6e78 40%,#bcc4d0 75%,#e4e7ee)}
.slide-arrow{position:absolute;top:112px;width:38px;height:38px;border-radius:50%;background:radial-gradient(#fff,#e6e6e6);box-shadow:0 1px 3px rgba(0,0,0,.3)}
.slide-arrow svg{position:absolute;left:11px;top:11px}
.slide-arrow.prev{left:3px}.slide-arrow.next{left:1008px}
.welcome-photo{position:absolute;left:43px;top:466px;width:247px;height:147px;border:2px solid #4d5f77;background:linear-gradient(135deg,#5a6f86,#c9d3de 55%,#3f4c5c)}
.welcome-title{position:absolute;left:301px;top:466px;font-family:"Open Sans",Arial,sans-serif;font-size:21px;color:var(--blue);font-weight:400}
.welcome-text{position:absolute;left:305px;top:502px;width:567px;font-size:13.4px;line-height:21px;text-align:justify;color:#333}
.divider{position:absolute;left:41px;top:629px;width:830px;height:1px;background:#b5b5b5}
.feature{position:absolute;top:641px;width:250px;height:223px}
.feature h3{height:35px;line-height:35px;color:#fff;font-size:16px;font-weight:700;padding-left:32px;position:relative;letter-spacing:.3px}
.feature h3::before{content:"";position:absolute;left:14px;top:13px;width:9px;height:9px;background:#fff;opacity:.75}
.feature-body{padding:12px 15px 0 16px;font-size:13.5px;line-height:21px;color:var(--muted)}
.feature-body p{margin-bottom:15px}
.feature .more{position:absolute;left:15px;bottom:10px;font-size:12.5px;color:#111}
.feature.green{left:42px;background:var(--green-body)}.feature.green h3{background:linear-gradient(#82c45c,#62a83c)}.feature.green em{color:var(--green-text)}
.feature.blue{left:326px;background:var(--blue-body)}.feature.blue h3{background:linear-gradient(#2a74b8,#164f8a)}.feature.blue em{color:var(--blue-text)}
.feature.amber{left:609px;background:var(--amber-body)}.feature.amber h3{background:linear-gradient(#e09a30,#c67c14)}.feature.amber em{color:var(--amber-text)}
.feature em{font-style:normal}
.services{position:absolute;left:907px;top:463px;width:267px;height:414px;background:var(--panel-grey);padding:0 3px 3px}
.services h2{height:49px;display:flex;align-items:center;gap:10px;padding-left:16px;font-family:"Open Sans",Arial,sans-serif;font-size:21px;font-weight:600;color:#555}
.services ul{list-style:none;background:#fff;height:362px;border:1px solid #c6c6c6;padding-top:30px}
.services li{position:relative;padding-left:45px;font-size:14px;color:#333;height:44.4px}
.services li svg{position:absolute;left:20px;top:2px}
.footer{position:absolute;left:0;top:888px;width:1200px;height:50px;background:var(--footer)}
.footer-nav{position:absolute;left:38px;top:18px;font-size:13px;color:#b8b8b8;display:flex}
.footer-nav span{margin:0 11px}
.copyright{position:absolute;right:34px;top:16px;font-size:13px;color:#b8b8b8}
</style>
</head>
<body>
<div class="topbar"></div>

<nav class="main-nav">
  <a href="#" style="left:534px">HOME</a>
  <a href="#" style="left:660px">ABOUT US</a>
  <a href="#" style="left:797px">SERVICES</a>
  <a href="#" style="left:942px">PRODUCTS</a>
  <a href="#" style="left:1093px">CONTACT</a>
</nav>

<a class="brand" href="#"><span class="brand-mark"></span><span class="brand-name">Quill Harbor</span></a>

<div class="social">
  <a class="s1" href="#" aria-label="Social link"></a>
  <a class="s2" href="#" aria-label="Social link"></a>
  <a class="s3" href="#" aria-label="Social link"></a>
</div>

<section class="hero">
  <a class="slide-arrow prev" href="#" aria-label="Previous slide"><svg width="16" height="16" viewBox="0 0 16 16"><path d="M10 3L5 8l5 5" fill="none" stroke="#777" stroke-width="2.5"/></svg></a>
  <h1 class="hero-title">Contrary To Popular Belief</h1>
  <p class="hero-sub">We Care....</p>
  <div class="hero-photo" role="img" aria-label="Photo of a smiling business team standing in a row"></div>
  <a class="slide-arrow next" href="#" aria-label="Next slide"><svg width="16" height="16" viewBox="0 0 16 16"><path d="M6 3l5 5-5 5" fill="none" stroke="#777" stroke-width="2.5"/></svg></a>
</section>

<div class="welcome-photo" role="img" aria-label="Photo of colleagues reviewing documents at a desk"></div>
<h2 class="welcome-title">Welcome to our Company</h2>
<p class="welcome-text">Lorem Ipsum is simply dummy text of the printing and typesetting industry. Lorem Ipsum has been the industry's standard dummy text ever since the 1500s, when an unknown printer took a galley of type and scrambled it to make a type specimen book. It has survived not only five centuries, but also the leap into electronic typesetting, remaining essentially unchanged. It was popularised in the 1960s with the release of Typeworth sheets containing</p>
<div class="divider"></div>

<article class="feature green">
  <h3>Consectetuer Adipiscing</h3>
  <div class="feature-body">
    <p><em>Lorem ipsum dolor sit amet sit consec adipiscing</em> elit ellentesque nec masa eleifend lectus.</p>
    <p>Dolor sit amet consectetuer elitq ellentesque nec massa eleifend lectus dolor sit amet.</p>
  </div>
  <a class="more" href="#">read more</a>
</article>
<article class="feature blue">
  <h3>Sectetuer Edipiscing</h3>
  <div class="feature-body">
    <p><em>Lorem ipsum dolor sit amet consectetuer adipiscing</em> elit nec massa eleifend lectus ipsum dolor sit amet</p>
    <p>Pellentesque nec massa eleifend lectus dolor sit amet.</p>
  </div>
  <a class="more" href="#">read more</a>
</article>
<article class="feature amber">
  <h3>Qensectet Vdipiscing</h3>
  <div class="feature-body">
    <p><em>Lorem ipsum dolor sit amet secteer adipiscing elit.</em> Entesque necmass eleifend lectus.</p>
    <p>Ipsum dolor sit amet consectetuer elit pellentesque nec massa elit eleifend lectus dolor sit.</p>
  </div>
  <a class="more" href="#">read more</a>
</article>

<aside class="services">
  <h2><svg width="22" height="20" viewBox="0 0 22 20"><path d="M4 11a7 7 0 0 1 12-5" fill="none" stroke="#d9501a" stroke-width="3"/><path d="M14 2l4 4-5 2z" fill="#d9501a"/><path d="M18 10a7 7 0 0 1-12 5" fill="none" stroke="#e9823a" stroke-width="3"/><path d="M8 19l-4-4 5-2z" fill="#e9823a"/></svg>Services</h2>
  <ul>
    <li><svg width="14" height="14" viewBox="0 0 14 14"><path d="M1 8l4 4 8-11" fill="none" stroke="var(--tick)" stroke-width="2.4"/></svg>Itera feugiat accumsan</li>
    <li><svg width="14" height="14" viewBox="0 0 14 14"><path d="M1 8l4 4 8-11" fill="none" stroke="var(--tick)" stroke-width="2.4"/></svg>Lorem ipsum</li>
    <li><svg width="14" height="14" viewBox="0 0 14 14"><path d="M1 8l4 4 8-11" fill="none" stroke="var(--tick)" stroke-width="2.4"/></svg>Dolor sit amet. Itera feuguit</li>
    <li><svg width="14" height="14" viewBox="0 0 14 14"><path d="M1 8l4 4 8-11" fill="none" stroke="var(--tick)" stroke-width="2.4"/></svg>Itera feugiat accumsan</li>
    <li><svg width="14" height="14" viewBox="0 0 14 14"><path d="M1 8l4 4 8-11" fill="none" stroke="var(--tick)" stroke-width="2.4"/></svg>Dolor sit amet. Itera feuguit</li>
    <li><svg width="14" height="14" viewBox="0 0 14 14"><path d="M1 8l4 4 8-11" fill="none" stroke="var(--tick)" stroke-width="2.4"/></svg>Itera feugiat accumsan</li>
    <li><svg width="14" height="14" viewBox="0 0 14 14"><path d="M1 8l4 4 8-11" fill="none" stroke="var(--tick)" stroke-width="2.4"/></svg>Lorem Ipsum</li>
  </ul>
</aside>

<footer class="footer">
  <nav class="footer-nav">
    <a href="#">HOME</a><span>|</span><a href="#">ABOUT US</a><span>|</span><a href="#">PRODUCTS</a><span>|</span><a href="#">SERVICES</a><span>|</span><a href="#">CONTACT US</a>
  </nav>
  <p class="copyright">Copyright © 2012 Quill Harbor Pty Ltd</p>
</footer>
</body>
</html>
```